Business Card Design (NEW FILES)

ATTENTION: New vector files are available. Please update your design to reflect/use the new (better resolution) logo images.

Seeking a unique and professional business card design for a commercial drone photography/videography business. The layout should feature
the logo (attached) and include the following information:
Owen Tarrick
614-502-7738
www.skylarkreelworks.example
NRD Certified Remote Pilot

Owen Tarrick

```html
<!DOCTYPE html>
<html lang="en">
<head>
<meta charset="utf-8">
<title>Skylark Reelworks — Business Card</title>
<link href="https://fonts.googleapis.com/css2?family=Open+Sans:wght@400;600;700&display=swap" rel="stylesheet">
<style>
  :root {
    --bg: #222222;
    --navy: #1b1c4f;
    --navy-deep: #15173f;
    --navy-light: #2c3a8f;
    --orange: #e8894a;
    --white: #ffffff;
  }
  * { box-sizing: border-box; margin: 0; padding: 0; }
  html, body {
    width: 1200px; height: 780px; overflow: hidden;
    background: var(--bg);
    font-family: "Open Sans", Arial, sans-serif;
  }
  .canvas { position: relative; width: 1200px; height: 780px; }

  /* Front of card (portrait) */
  .card-front {
    position: absolute; left: 210px; top: 120px;
    width: 320px; height: 560px;
    background: var(--navy);
    overflow: hidden;
    box-shadow: 0 18px 40px rgba(0,0,0,.55);
  }
  .card-front__header {
    height: 180px; background: var(--white);
    display: flex; align-items: center; justify-content: center; gap: 10px;
  }
  .brand-dot {
    width: 18px; height: 18px; border-radius: 50%; background: var(--orange);
  }
  .brand-name {
    font-weight: 600; font-size: 22px; color: var(--navy); letter-spacing: .5px;
  }
  .card-front__details {
    position: absolute; right: 40px; bottom: 46px;
    text-align: right; color: var(--white);
  }
  .person-name { font-size: 30px; font-weight: 700; line-height: 1.1; }
  .person-name__first { color: var(--orange); }
  .person-role { font-size: 15px; margin-bottom: 14px; }
  .credential { font-size: 14px; line-height: 1.45; }
  .contact-list { list-style: none; margin-top: 18px; font-size: 14px; line-height: 1.8; }
  .contact-list li { display: flex; justify-content: flex-end; align-items: center; gap: 8px; }
  .contact-list svg { width: 14px; height: 14px; flex: none; }
  .accent-tab {
    position: absolute; right: 0; top: 392px;
    width: 14px; height: 60px; background: var(--orange);
  }

  /* Back of card (landscape) */
  .card-back {
    position: absolute; left: 600px; top: 240px;
    width: 560px; height: 320px;
    background: var(--navy-deep);
    overflow: hidden;
    box-shadow: 0 18px 40px rgba(0,0,0,.55);
  }
  .card-back__brand {
    position: absolute; left: 40px; top: 60px;
    display: flex; align-items: center; gap: 10px;
  }
  .card-back__brand .brand-name { color: var(--white); font-size: 20px; }
  .card-back__art {
    position: absolute; left: 240px; top: 30px; width: 290px; height: 200px;
    border-radius: 50%;
    background: radial-gradient(ellipse at center, var(--navy-light) 0%, rgba(44,58,143,.35) 45%, rgba(21,23,63,0) 72%);
  }
</style>
</head>
<body>
<main class="canvas">

  <section class="card-front" aria-label="Business card front">
    <header class="card-front__header">
      <span class="brand-dot"></span>
      <span class="brand-name">Skylark Reelworks</span>
    </header>

    <div class="card-front__details">
      <p class="person-name"><span class="person-name__first">Owen</span> Tarrick</p>
      <p class="person-role">Owner</p>
      <p class="credential">NRD Certified Remote Pilot</p>
      <p class="credential">Fully Insured</p>
      <ul class="contact-list">
        <li>614-502-7738
          <svg viewBox="0 0 24 24" aria-hidden="true"><path fill="#e8894a" d="M6.6 10.8a15 15 0 0 0 6.6 6.6l2.2-2.2c.3-.3.7-.4 1-.2 1.1.4 2.3.6 3.6.6.6 0 1 .4 1 1V20c0 .6-.4 1-1 1A17 17 0 0 1 3 4c0-.6.4-1 1-1h3.5c.6 0 1 .4 1 1 0 1.3.2 2.5.6 3.6.1.3 0 .7-.2 1z"/></svg>
        </li>
        <li>www.skylarkreelworks.example
          <svg viewBox="0 0 24 24" aria-hidden="true"><circle cx="12" cy="12" r="9" fill="none" stroke="#e8894a" stroke-width="2"/><path d="M3 12h18M12 3c3 3 3 15 0 18M12 3c-3 3-3 15 0 18" fill="none" stroke="#e8894a" stroke-width="1.6"/></svg>
        </li>
      </ul>
    </div>
    <span class="accent-tab"></span>
  </section>

  <section class="card-back" aria-label="Business card back">
    <div class="card-back__brand">
      <span class="brand-dot"></span>
      <span class="brand-name">Skylark Reelworks</span>
    </div>
    <div class="card-back__art" role="img" aria-label="Embossed drone illustration with a colourful camera aperture"></div>
  </section>

</main>
</body>
</html>
```